Elevating our current Business Card Design

We want to elevate our current business card with a new design to look like a zenith 300 company. We are a premium lubricant distributor (oil and grease).
We need 2 versions, version 1 is as per the uploaded a copy of our current business card with the English version.
For our Chinese version we need to use the front to be English in English and have the back of the card designed exactly like the front for all info to be in Chinese.
The design template needs to be such that we can amend the template with adding different information for each person's card.
The background colour of the card can be changed- we just need to clearly see all information on the card and logos.
The QJR and Ember steady logos cannot have any colour or display changes- only use the logos attached.
All logos need to be included and all information from the attached current card

```html
<!DOCTYPE html>
<html lang="en">
<head>
<meta charset="utf-8">
<title>Orvane Business Card</title>
<link href="https://fonts.googleapis.com/css2?family=Open+Sans:wght@400;600;700;800&display=swap" rel="stylesheet">
<style>
  :root {
    --stage: #232323;
    --card: #1e1e21;
    --card-layer: #28282c;
    --card-layer-deep: #242428;
    --red: #ee2b24;
    --red-deep: #c41d1d;
    --white: #ffffff;
    --gold: #f0b12a;
    --orange: #f47a20;
    --grey: #8d8d92;
  }
  * { margin: 0; padding: 0; box-sizing: border-box; }
  html, body { width: 1200px; height: 780px; overflow: hidden; background: var(--stage); }
  body { font-family: "Open Sans", Arial, sans-serif; color: var(--white); position: relative; }

  .card {
    position: absolute; top: 40px; width: 428px; height: 700px;
    background: var(--card); border-radius: 26px; overflow: hidden;
    box-shadow: 0 14px 34px rgba(0,0,0,.55);
  }
  .card--front { left: 130px; }
  .card--back { left: 642px; }

  /* Front */
  .front-mark {
    position: absolute; inset: 0; display: flex; align-items: center; justify-content: center; gap: 18px;
  }
  .front-mark__dot { width: 34px; height: 34px; border-radius: 50%; background: var(--gold); }
  .front-mark__name { font-size: 62px; font-weight: 800; color: var(--red); letter-spacing: 2px; }

  /* Back */
  .back-curves { position: absolute; inset: 0; }
  .back-content { position: relative; text-align: center; }
  .brand { display: flex; align-items: center; justify-content: center; gap: 12px; padding-top: 58px; }
  .brand__dot { width: 18px; height: 18px; border-radius: 50%; background: var(--gold); }
  .brand__name { font-size: 40px; font-weight: 800; color: var(--red); letter-spacing: 1px; }

  .person__name { margin-top: 34px; font-size: 34px; font-weight: 700; color: var(--red); line-height: 1.1; }
  .person__role { font-size: 17px; font-weight: 600; margin-top: 4px; }

  .icon-row { display: flex; justify-content: center; gap: 12px; margin-top: 18px; }
  .icon {
    width: 28px; height: 24px; border-radius: 6px; background: var(--red);
    display: flex; align-items: center; justify-content: center;
  }
  .icon svg { width: 15px; height: 15px; }

  .contact { list-style: none; margin-top: 14px; font-size: 16px; line-height: 1.5; }
  .address-icon { display: flex; justify-content: center; margin-top: 18px; }
  .address { margin-top: 12px; font-size: 16.5px; line-height: 1.4; }

  .partners { position: absolute; left: 0; right: 0; bottom: 42px; padding: 0 34px; }
  .partners__top { display: flex; align-items: center; justify-content: space-between; }
  .partner-name { display: flex; align-items: center; gap: 6px; font-size: 14px; font-weight: 700; }
  .partner-name__dot { width: 12px; height: 12px; border-radius: 50%; background: var(--white); }
  .cert-badges { display: flex; gap: 14px; }
  .cert-badge {
    width: 42px; height: 42px; border-radius: 50%; background: var(--orange);
    border: 4px solid var(--grey);
  }
  .distributor-band {
    margin-top: 16px; display: flex; height: 54px; border: 2px solid var(--red); border-radius: 2px;
  }
  .distributor-band__name {
    flex: 1; display: flex; align-items: center; justify-content: center;
    font-size: 13px; font-weight: 700; color: var(--red); text-transform: uppercase;
  }
  .distributor-band__supplier {
    flex: 1; background: var(--red); display: flex; flex-direction: column; align-items: center; justify-content: center;
  }
  .supplier__name { font-size: 20px; font-weight: 800; letter-spacing: 1px; line-height: 1; }
  .supplier__tag { font-size: 9px; font-weight: 600; letter-spacing: 1px; margin-top: 3px; }
</style>
</head>
<body>

  <section class="card card--front" aria-label="Card front">
    <div class="front-mark">
      <span class="front-mark__dot"></span>
      <span class="front-mark__name">ORVANE</span>
    </div>
  </section>

  <section class="card card--back" aria-label="Card back">
    <svg class="back-curves" viewBox="0 0 428 700" preserveAspectRatio="none" aria-hidden="true">
      <path d="M0 470 Q150 520 428 380 L428 700 L0 700 Z" fill="var(--card-layer)"/>
      <path d="M0 560 Q190 560 428 440 L428 700 L0 700 Z" fill="var(--card-layer-deep)"/>
      <path d="M0 470 Q150 520 428 380" fill="none" stroke="#151517" stroke-width="3" opacity=".6"/>
    </svg>

    <div class="back-content">
      <div class="brand">
        <span class="brand__dot"></span>
        <span class="brand__name">ORVANE</span>
      </div>

      <h1 class="person__name">Dana Whitcombe</h1>
      <p class="person__role">Administration Executive</p>

      <div class="icon-row">
        <span class="icon" aria-label="Phone">
          <svg viewBox="0 0 16 16"><path d="M4 2 L6 5 L5 6.5 Q6.5 9.5 9.5 11 L11 10 L14 12 L13 14 Q7 14 2 3 Z" fill="#fff"/></svg>
        </span>
        <span class="icon" aria-label="Fax">
          <svg viewBox="0 0 16 16"><rect x="4" y="2" width="8" height="4" fill="#fff"/><rect x="2" y="7" width="12" height="7" rx="1" fill="#fff"/></svg>
        </span>
        <span class="icon" aria-label="Email">
          <svg viewBox="0 0 16 16"><rect x="2" y="4" width="12" height="9" fill="#fff"/><path d="M2 4 L8 9 L14 4" fill="none" stroke="#ee2b24" stroke-width="1.4"/></svg>
        </span>
        <span class="icon" aria-label="Website">
          <svg viewBox="0 0 16 16"><circle cx="8" cy="8" r="6" fill="none" stroke="#fff" stroke-width="1.6"/><path d="M2 8 H14 M8 2 Q4 8 8 14 Q12 8 8 2" fill="none" stroke="#fff" stroke-width="1.2"/></svg>
        </span>
      </div>

      <ul class="contact">
        <li>1300 000 417 (Phone)</li>
        <li>+61 400 000 291 (Mobile)</li>
        <li>+61 8 9000 0356 (Fax)</li>
        <li>dana.whitcombe@orvanedirect.com</li>
        <li>www.orvanedirect.com</li>
      </ul>

      <div class="address-icon">
        <span class="icon" aria-label="Address">
          <svg viewBox="0 0 16 16"><path d="M8 1 Q13 1 13 6 Q13 9 8 15 Q3 9 3 6 Q3 1 8 1 Z" fill="#fff"/><circle cx="8" cy="6" r="2" fill="#ee2b24"/></svg>
        </span>
      </div>
      <p class="address">48 Freightway Drive<br>Alderton, WA 6999</p>
    </div>

    <div class="partners">
      <div class="partners__top">
        <span class="partner-name"><span class="partner-name__dot"></span>Ember steady</span>
        <div class="cert-badges">
          <span class="cert-badge" role="img" aria-label="Certification badge"></span>
          <span class="cert-badge" role="img" aria-label="Certification badge"></span>
          <span class="cert-badge" role="img" aria-label="Certification badge"></span>
        </div>
      </div>
      <div class="distributor-band">
        <div class="distributor-band__name">Orvane Lubricant Distributors</div>
        <div class="distributor-band__supplier">
          <span class="supplier__name">HALVERA</span>
          <span class="supplier__tag">PREMIUM LUBRICANTS</span>
        </div>
      </div>
    </div>
  </section>

</body>
</html>
```